Business Card for Coastal Tundrabridge Advisory

We need a business card for Coastal Tundrabridge Advisory. The company website address is provided below. The company logo is attached. We provide specialized permafrost services to the mining, transportation, and oil & gas industries. The card should be prepared for:
Matthias Korhonen, PhD.
Coastal Tundrabridge Advisory
PO Box 418259
Quillwater, Alaska 99642
Direct: +1-907-555-0143
Email: mkorhonen@tundrabridgeadvisory.example
Website: www.coastaltundrabridgeadvisory.example

```html
<!DOCTYPE html>
<html lang="en">
<head>
<meta charset="utf-8">
<title>Coastal Tundrabridge Advisory — Business Card</title>
<link href="https://fonts.googleapis.com/css2?family=Roboto:wght@300;400;500;700&display=swap" rel="stylesheet">
<style>
  :root {
    --backdrop: #262626;
    --card: #111723;
    --ink: #ffffff;
    --ink-soft: #d9dee6;
    --ice: #3aa6e0;
    --ice-deep: #1d4f74;
    --rule: #8a93a0;
  }
  * { box-sizing: border-box; margin: 0; padding: 0; }
  html, body {
    width: 1200px; height: 711px; overflow: hidden;
    background: var(--backdrop);
    font-family: "Roboto", sans-serif;
    color: var(--ink);
  }
  .stage {
    position: relative; width: 1200px; height: 711px;
    display: flex; align-items: center; justify-content: center; gap: 40px;
  }
  .card {
    position: relative; width: 540px; height: 308px;
    background: var(--card);
    box-shadow: 0 10px 30px rgba(0,0,0,.55);
    overflow: hidden;
  }

  /* Front */
  .pattern-field {
    position: absolute; inset: 0;
    background:
      linear-gradient(200deg, rgba(58,166,224,.55) 0%, rgba(29,79,116,.35) 30%, rgba(17,23,35,0) 58%),
      repeating-linear-gradient(180deg, rgba(255,255,255,.025) 0 8px, rgba(255,255,255,0) 8px 16px);
  }
  .brand {
    position: absolute; left: 0; right: 0; top: 92px;
    text-align: center;
  }
  .brand-name {
    font-weight: 700; font-size: 34px; letter-spacing: 1px; color: var(--ink);
  }
  .brand-line {
    margin-top: 8px; font-weight: 400; font-size: 11px; letter-spacing: 6px;
    text-transform: uppercase; color: var(--ink-soft);
  }
  .services {
    position: absolute; left: 24px; right: 24px; bottom: 34px; text-align: center;
  }
  .services-title {
    font-weight: 500; font-size: 11px; letter-spacing: .5px; margin-bottom: 6px;
  }
  .services-text { font-size: 10.5px; color: var(--ink-soft); }

  /* Back */
  .holder {
    position: absolute; left: 40px; top: 96px; width: 210px; text-align: right;
  }
  .holder-name { font-size: 26px; line-height: 1.1; }
  .holder-first { font-weight: 700; }
  .holder-last { font-weight: 300; display: block; }
  .holder-title { font-weight: 700; font-size: 14px; margin-top: 4px; }
  .divider {
    position: absolute; left: 272px; top: 74px; width: 1px; height: 118px;
    background: var(--rule);
  }
  .contacts {
    position: absolute; left: 292px; top: 92px; list-style: none;
    font-size: 10px; color: var(--ink-soft);
  }
  .contacts li { display: flex; align-items: center; gap: 8px; margin-bottom: 12px; }
  .contacts svg { width: 12px; height: 12px; flex: none; }
  .address {
    position: absolute; left: 0; right: 0; bottom: 40px; text-align: center;
    font-size: 12px; color: var(--ink-soft);
  }
</style>
</head>
<body>
<main class="stage">
  <section class="card card-front">
    <div class="pattern-field" role="img" aria-label="Repeating brand wordmark pattern fading from ice blue to navy"></div>
    <div class="brand">
      <div class="brand-name">Coastal Tundrabridge</div>
      <div class="brand-line">Advisory</div>
    </div>
    <div class="services">
      <p class="services-title">OUR SERVICES</p>
      <p class="services-text">We provide specialized permafrost services to the mining, transportation, and oil &amp; gas industries</p>
    </div>
  </section>

  <section class="card card-back">
    <div class="holder">
      <p class="holder-name"><span class="holder-first">Matthias</span> <span class="holder-last">Korhonen</span></p>
      <p class="holder-title">PhD</p>
    </div>
    <div class="divider"></div>
    <ul class="contacts">
      <li>
        <svg viewBox="0 0 24 24" fill="#fff"><path d="M6.6 10.8a15.1 15.1 0 0 0 6.6 6.6l2.2-2.2c.3-.3.7-.4 1-.2 1.1.4 2.3.6 3.6.6.6 0 1 .4 1 1V20c0 .6-.4 1-1 1A17 17 0 0 1 3 4c0-.6.4-1 1-1h3.5c.6 0 1 .4 1 1 0 1.3.2 2.5.6 3.6.1.3 0 .7-.2 1z"/></svg>
        +1-907-555-0143
      </li>
      <li>
        <svg viewBox="0 0 24 24" fill="none" stroke="#fff" stroke-width="2"><rect x="3" y="5" width="18" height="14" rx="1"/><path d="M3 6l9 7 9-7"/></svg>
        mkorhonen@tundrabridgeadvisory.example
      </li>
      <li>
        <svg viewBox="0 0 24 24" fill="none" stroke="#fff" stroke-width="2"><circle cx="12" cy="12" r="9"/><path d="M3 12h18M12 3c3 3.5 3 14.5 0 18M12 3c-3 3.5-3 14.5 0 18"/></svg>
        www.coastaltundrabridgeadvisory.example
      </li>
    </ul>
    <p class="address">PO Box 418259 Quillwater, Alaska 99642</p>
  </section>
</main>
</body>
</html>
```